PowerPoint Corporate Template for Healthcare AI Technology Company

Take logo and create a comprehensive source file for corporate PowerPoint presentation library that provides an array of title/separator slides, graphic presentation options, chart options and text slide options. Utilize the current logo files and provide options on white backgrounds, and knock out options.

Target Market(s)

Pharmaceutical Manufacturers

Font styles to use
Sans Serif

Colors
6b449b
0556a4
33a6d7
0393ce
ffffff
e34197

Requirements
Must have
• Use logos upgraded in files; create an embedded color palette that aligns to the logo; include multiple options for different types of slides including charts; create a bullet point that is the logo in the purple/blue color with white background; incorporate knock out logo version option for separator pages; must include page numbers; use font aligned to logo for text slide options
Nice to have
• Tech looking, data intensive slide options that communicate easily; could be using 3-4 data points per slide
Should not have
• Any logo other than what has been shared

```html
<!DOCTYPE html>
<html lang="en">
<head>
<meta charset="utf-8">
<title>Veritra Presentation Deck</title>
<link href="https://fonts.googleapis.com/css2?family=Poppins:wght@300;400;500;600;700&family=Montserrat:wght@300;400;500;600&display=swap" rel="stylesheet">
<style>
:root{
  --purple:#6a56aa;
  --violet:#6b449b;
  --blue:#4e7fc4;
  --teal:#1fc3d6;
  --ink:#2a2a33;
  --text:#555;
  --muted:#9a9aa8;
  --line:#e4e5ef;
  --dark:#1e1e22;
  --white:#ffffff;
  --grad:linear-gradient(165deg,#6d4aa3 0%,#5a72bd 45%,#24c1d6 100%);
  --grad-h:linear-gradient(180deg,#24bfd6 0%,#5a7cc2 60%,#6b52a8 100%);
}
*{box-sizing:border-box;margin:0;padding:0}
html,body{width:1200px;height:2563px;overflow:hidden;background:var(--white)}
body{position:relative;font-family:"Montserrat",sans-serif;color:var(--ink)}
.abs{position:absolute}
.photo{position:absolute}

/* hero */
.hero-photo{left:0;top:0;width:1200px;height:495px;background:linear-gradient(180deg,#cfc8c1 0%,#dedad6 45%,#eeedf2 80%,#fff 100%)}
.hero-title{left:70px;top:178px;font-family:"Poppins",sans-serif;line-height:1}
.hero-title .line-1{display:block;font-size:66px;font-weight:700;color:var(--purple);letter-spacing:-1px}
.hero-title .line-2{display:block;font-size:62px;font-weight:400;color:var(--ink);margin-left:128px;margin-top:-2px}
.hero-slide{left:560px;top:82px;width:480px;height:270px;background:var(--grad);overflow:hidden;box-shadow:0 6px 24px rgba(40,40,70,.25)}
.hero-slide .top-band{height:58px}

/* brand */
.brand{display:flex;align-items:center;justify-content:center;gap:5px;font-family:"Poppins",sans-serif;font-weight:300;color:var(--purple)}
.brand .dot{border:1.5px solid currentColor;border-radius:50%}
.brand.on-dark{color:var(--white)}

/* slide */
.slide{position:absolute;width:386px;height:217px;background:var(--white);overflow:hidden;box-shadow:0 0 0 1px #eceef4}
.slide.last{top:2343px}
.top-band{position:absolute;left:0;top:0;width:100%;height:45px;background:var(--white);display:flex;align-items:center;justify-content:center}
.grad{background:var(--grad)}
.cover-title{position:absolute;width:100%;text-align:center;font-family:"Poppins",sans-serif;font-weight:600;font-size:14px;color:var(--white)}
.cover-sub{position:absolute;width:100%;text-align:center;font-size:4.5px;letter-spacing:2.5px;color:var(--white)}
.cover-by{position:absolute;width:100%;text-align:center;font-size:4px;letter-spacing:2px;color:var(--white);line-height:1.4}
.cover-by b{letter-spacing:.5px}
.dark-text{color:var(--ink)}
.socials{position:absolute;width:100%;display:flex;justify-content:center;gap:3px}
.socials i{width:8px;height:8px;border:1px solid currentColor;border-radius:50%;display:block}

.hdr{position:absolute;top:10px;left:0;width:100%;text-align:center;font-family:"Poppins",sans-serif;font-size:12px;font-weight:300;color:var(--ink);line-height:1.1}
.hdr .sub{display:block;font-family:"Montserrat",sans-serif;font-size:5px;font-weight:600;letter-spacing:1.6px;color:var(--purple)}
.hdr.on-grad{color:var(--white);font-size:14px;top:20px}
.hdr.on-grad .sub{color:var(--white)}
.hdr.left{text-align:left}
.head-band{position:absolute;left:0;top:0;width:100%;height:62px;background:var(--grad-h)}
.tab{position:absolute;left:186px;top:0;width:20px;height:9px;background:var(--purple)}

.foot{position:absolute;left:0;bottom:0;width:100%;height:14px}
.foot .copy{position:absolute;left:18px;bottom:6px;font-size:3.5px;color:var(--muted)}
.foot .pg{position:absolute;left:183px;bottom:12px;width:20px;height:3px;background:var(--purple)}
.foot .num{position:absolute;left:183px;width:20px;bottom:4px;text-align:center;font-size:3.5px;color:var(--muted)}
.foot .brand{position:absolute;right:14px;bottom:3px;font-size:7px}
.foot .brand .dot{width:7px;height:7px;border-width:1px}

.tiny{font-size:3.6px;line-height:1.45;color:var(--text)}
.label{font-size:4.5px;font-weight:600;color:var(--purple)}
.icon-ring{position:absolute;width:12px;height:12px;border:1.2px solid #9aa7e0;border-radius:50%}
.item{position:absolute;width:150px}
.item .icon-ring{left:0;top:2px}
.item .label,.item .tiny{margin-left:18px}

.card{position:absolute;color:var(--white);border-radius:6px;padding:6px 7px}
.card h4{font-size:5px;font-weight:600;margin-bottom:3px}
.card p{font-size:3.6px;line-height:1.4}
.pv{background:#6b5cae}
.tl{background:#25bfd5}

.pct{font-family:"Poppins",sans-serif;font-weight:600;color:var(--ink)}
.bubble{position:absolute;border-radius:50%;color:var(--white);text-align:center;display:flex;flex-direction:column;justify-content:center;align-items:center}
.bubble b{font-size:5px;font-weight:600}
.bubble span{font-size:3px;line-height:1.3;padding:0 6px}
</style>
</head>
<body>

<!-- hero -->
<div class="photo hero-photo" role="img" aria-label="Photo of friends raising their hands against a bright evening sky"></div>
<h1 class="abs hero-title"><span class="line-1">Presentation</span><span class="line-2">Deck</span></h1>

<section class="abs hero-slide">
  <div class="top-band" style="height:58px"><div class="brand" style="font-size:20px"><span class="dot" style="width:20px;height:20px"></span>Veritra</div></div>
  <div class="cover-title" style="top:125px;font-size:19px">Prestation Title Goes Here</div>
  <div class="cover-sub" style="top:158px;font-size:6px;letter-spacing:3.5px">SUB TITLE GOES HERE</div>
  <div class="cover-by" style="top:205px;font-size:5.5px;letter-spacing:3px">PRESENTED BY<br><b>Presenter name</b></div>
  <div class="socials" style="top:230px;color:#fff;gap:4px"><i style="width:11px;height:11px"></i><i style="width:11px;height:11px"></i><i style="width:11px;height:11px"></i></div>
</section>

<!-- row 1 -->
<section class="slide grad" style="left:15px;top:501px">
  <div class="top-band"><div class="brand" style="font-size:15px"><span class="dot" style="width:15px;height:15px"></span>Veritra</div></div>
  <div class="cover-title" style="top:102px">Prestation Title Goes Here</div>
  <div class="cover-sub" style="top:126px">SUB TITLE GOES HERE</div>
  <div class="cover-by" style="top:166px">PRESENTED BY<br><b>Presenter name</b></div>
  <div class="socials" style="top:185px;color:#fff"><i></i><i></i><i></i></div>
</section>

<section class="slide" style="left:410px;top:501px">
  <div class="photo" style="left:0;top:0;width:386px;height:155px;background:linear-gradient(160deg,#f3f5f9,#e6eaf1 60%,#f7f8fb)" role="img" aria-label="Pale photo of glass office towers"></div>
  <div class="abs" style="left:184px;top:42px;width:18px;height:18px;border:1.5px solid var(--purple);border-radius:50%"></div>
  <div class="cover-title dark-text" style="top:86px">Prestation Title Goes Here</div>
  <div class="cover-sub" style="top:110px;color:var(--text)">SUB TITLE GOES HERE</div>
  <div class="abs" style="left:0;top:155px;width:386px;height:62px;background:#6a6bb8"></div>
  <div class="cover-by" style="top:175px">PRESENTED BY<br><b>Presenter name</b></div>
</section>

<section class="slide" style="left:805px;top:501px">
  <div class="photo" style="left:0;top:0;width:195px;height:217px;background:var(--dark)" role="img" aria-label="Dark panel with a pattern of circles"></div>
  <div class="abs brand on-dark" style="left:0;top:96px;width:195px;font-size:19px"><span class="dot" style="width:19px;height:19px"></span>Veritra</div>
  <div class="abs" style="left:200px;top:62px;width:186px;text-align:center;font-family:Poppins,sans-serif;font-weight:600;font-size:14px;line-height:1.2">Prestation Title<br>Goes Here</div>
  <div class="abs" style="left:200px;top:102px;width:186px;text-align:center;font-size:4.5px;letter-spacing:2px;color:var(--text)">SUB TITLE GOES HERE</div>
  <div class="abs" style="left:200px;top:168px;width:186px;text-align:center;font-size:4px;letter-spacing:2px;color:var(--text);line-height:1.4">PRESENTED BY<br><b style="letter-spacing:.5px">Presenter name</b></div>
  <div class="socials" style="left:97px;top:195px;color:var(--text)"><i></i><i></i><i></i></div>
  <div class="abs" style="left:180px;top:212px;width:22px;height:5px;background:var(--purple)"></div>
</section>

<!-- row 2 -->
<section class="slide" style="left:15px;top:731px">
  <div class="photo" style="left:0;top:0;width:386px;height:185px;background:var(--dark)" role="img" aria-label="Dark panel with a pattern of circles"></div>
  <div class="cover-title" style="top:87px">Prestation Title Goes Here</div>
  <div class="cover-sub" style="top:108px">SUB TITLE GOES HERE</div>
  <div class="cover-by" style="top:165px">PRESENTED BY<br><b>Presenter name</b></div>
  <div class="abs brand" style="left:0;top:193px;width:386px;font-size:12px"><span class="dot" style="width:12px;height:12px"></span>Veritra</div>
</section>

<section class="slide" style="left:410px;top:731px;background:linear-gradient(120deg,#6a4ea8 0%,#5c68b8 50%,#2fb3d3 100%)">
  <div class="photo" style="left:200px;top:0;width:186px;height:217px;background:radial-gradient(circle at 60% 45%,rgba(120,200,235,.45),rgba(90,110,200,0) 70%)" role="img" aria-label="Faint network of linked circles"></div>
  <div class="abs" style="left:12px;top:60px;font-family:Poppins,sans-serif;font-size:50px;font-weight:600;color:rgba(255,255,255,.18);line-height:1">01</div>
  <div class="abs" style="left:33px;top:80px;font-family:Poppins,sans-serif;font-size:29px;font-weight:300;color:#fff;line-height:1">Slide<br>Break</div>
  <p class="abs tiny" style="left:33px;top:146px;width:190px;color:#fff">Lorem ipsum dolor sit amet, consectetur adipiscing elit, sed do eiusmod tempor incididunt ut labore et dolore magna aliqua. Ut enim ad minim veniam, quis nostrud exercitation ullamco laboris nisi ut aliquip.</p>
</section>

<section class="slide" style="left:805px;top:731px">
  <div class="hdr">Add Awesome Title Here<span class="sub">ADD SUBTITLE HERE</span></div>
  <div class="photo" style="left:0;top:60px;width:60px;height:120px;background:radial-gradient(circle at 20% 60%,#dfe8f5,rgba(255,255,255,0) 70%)" role="img" aria-label="Faint network decoration"></div>
  <div class="photo" style="left:300px;top:30px;width:86px;height:90px;background:radial-gradient(circle at 60% 40%,#eceef6,rgba(255,255,255,0) 70%)" role="img" aria-label="Faint network decoration"></div>
  <div class="foot"><span class="copy">Copyright © | All Rights Reserved</span><span class="pg"></span><span class="num">6</span><div class="brand"><span class="dot"></span>Veritra</div></div>
</section>

<!-- row 3 -->
<section class="slide" style="left:15px;top:959px">
  <div class="head-band"></div><div class="tab"></div>
  <div class="hdr on-grad">Add Awesome Title Here<span class="sub">ADD SUBTITLE HERE</span></div>
  <div class="item" style="left:28px;top:74px"><span class="icon-ring"></span><div class="label">Project name</div><p class="tiny">Lorem ipsum dolor sit amet, nec an dictas equidem appellantur, ut has commune accommodare.</p></div>
  <div class="item" style="left:208px;top:74px"><span class="icon-ring"></span><div class="label">Project name</div><p class="tiny">Lorem ipsum dolor sit amet, nec an dictas equidem appellantur, ut has commune accommodare.</p></div>
  <div class="item" style="left:28px;top:115px"><span class="icon-ring"></span><div class="label">Project name</div><p class="tiny">Lorem ipsum dolor sit amet, nec an dictas equidem appellantur, ut has commune accommodare.</p></div>
  <div class="item" style="left:208px;top:115px"><span class="icon-ring"></span><div class="label">Project name</div><p class="tiny">Lorem ipsum dolor sit amet, nec an dictas equidem appellantur, ut has commune accommodare.</p></div>
  <div class="item" style="left:28px;top:156px"><span class="icon-ring"></span><div class="label">Project name</div><p class="tiny">Lorem ipsum dolor sit amet, nec an dictas equidem appellantur, ut has commune accommodare.</p></div>
  <div class="item" style="left:208px;top:156px"><span class="icon-ring"></span><div class="label">Project name</div><p class="tiny">Lorem ipsum dolor sit amet, nec an dictas equidem appellantur, ut has commune accommodare.</p></div>
  <div class="foot"><span class="copy">Copyright © | All Rights Reserved</span><span class="pg"></span><span class="num">7</span><div class="brand"><span class="dot"></span>Veritra</div></div>
</section>

<section class="slide" style="left:410px;top:959px">
  <div class="head-band"></div><div class="tab"></div>
  <div class="hdr on-grad">Add Awesome Title Here<span class="sub">ADD SUBTITLE HERE</span></div>
  <svg class="abs" style="left:0;top:0" width="386" height="217" viewBox="0 0 386 217">
    <line x1="58" y1="130" x2="352" y2="130" stroke="#333" stroke-width="1.6"/>
    <circle cx="40" cy="128" r="4" fill="none" stroke="#6a56aa" stroke-width="1.2"/>
    <g fill="#25bfd5"><circle cx="88" cy="130" r="2.2"/><circle cx="145" cy="130" r="2.2"/><circle cx="202" cy="130" r="2.2"/><circle cx="259" cy="130" r="2.2"/><circle cx="316" cy="130" r="2.2"/></g>
  </svg>
  <div class="abs" style="left:80px;top:114px;font-size:6px;font-weight:600">2001</div>
  <div class="abs" style="left:137px;top:140px;font-size:6px;font-weight:600">2019</div>
  <div class="abs" style="left:194px;top:114px;font-size:6px;font-weight:600">2020</div>
  <div class="abs" style="left:251px;top:140px;font-size:6px;font-weight:600">2021</div>
  <div class="abs" style="left:308px;top:114px;font-size:6px;font-weight:600">2022</div>
  <p class="abs tiny" style="left:115px;top:88px;width:60px;text-align:center">Sed ut perspiciatis unde omnis iste natus error sit</p>
  <p class="abs tiny" style="left:230px;top:88px;width:60px;text-align:center">Sed ut perspiciatis unde omnis iste natus error sit</p>
  <p class="abs tiny" style="left:58px;top:142px;width:60px;text-align:center">Sed ut perspiciatis unde omnis iste natus error sit</p>
  <p class="abs tiny" style="left:172px;top:142px;width:60px;text-align:center">Sed ut perspiciatis unde omnis iste natus error sit</p>
  <p class="abs tiny" style="left:286px;top:142px;width:60px;text-align:center">Sed ut perspiciatis unde omnis iste natus error sit</p>
  <div class="foot"><span class="copy">Copyright © | All Rights Reserved</span><span class="pg"></span><span class="num">8</span><div class="brand"><span class="dot"></span>Veritra</div></div>
</section>

<section class="slide" style="left:805px;top:959px">
  <div class="hdr">Add Awesome Title Here<span class="sub">ADD SUBTITLE HERE</span></div>
  <div class="abs tiny" style="left:22px;top:62px;width:342px">
    <p style="margin-bottom:5px">Lorem ipsum dolor sit amet, consectetur adipiscing elit, sed do eiusmod tempor incididunt ut labore et dolore magna aliqua. Lorem ipsum dolor sit amet, consectetur adipiscing elit, sed do eiusmod tempor incididunt ut labore.</p>
    <p style="margin-bottom:5px">Lorem ipsum dolor sit amet, consectetur adipiscing elit, sed do eiusmod tempor incididunt ut labore et dolore magna aliqua. Ut enim ad minim veniam, quis nostrud exercitation ullamco laboris nisi ut aliquip ex ea commodo consequat.</p>
    <p style="margin-bottom:5px">Lorem ipsum dolor sit amet, consectetur adipiscing elit, sed do eiusmod tempor incididunt ut labore et dolore magna aliqua. Duis aute irure dolor in reprehenderit in voluptate velit esse cillum dolore eu fugiat nulla pariatur. Excepteur sint occaecat cupidatat non proident, sunt in culpa qui officia deserunt mollit anim id est laborum.</p>
    <p>Lorem ipsum dolor sit amet, consectetur adipiscing elit, sed do eiusmod tempor incididunt ut labore et dolore magna aliqua. Lorem ipsum dolor sit amet.</p>
  </div>
  <div class="foot"><span class="copy">Copyright © | All Rights Reserved</span><span class="pg"></span><span class="num">9</span><div class="brand"><span class="dot"></span>Veritra</div></div>
</section>

<!-- row 4 -->
<section class="slide" style="left:15px;top:1189px">
  <div class="photo" style="left:0;top:0;width:228px;height:142px;background:linear-gradient(135deg,#1b2233,#2c3b5e 60%,#3b4f7a);border-bottom-right-radius:28px" role="img" aria-label="Photo of code on a computer screen"></div>
  <div class="card" style="left:192px;top:46px;width:104px;height:78px;background:rgba(107,92,174,.92);border-radius:10px;padding:10px">
    <div style="font-family:Poppins,sans-serif;font-size:10px;font-weight:600;margin-bottom:4px">01.</div>
    <h4>Your Text Here</h4>
    <p>Lorem ipsum dolor sit amet, consectetur adipiscing elit, sed do eiusmod tempor incididunt ut labore.</p>
  </div>
  <div class="abs" style="left:24px;top:160px;font-family:Poppins,sans-serif;font-size:22px;font-weight:300;color:var(--ink)">Your <b style="font-weight:600;color:var(--purple)">Awesome</b> Text Here</div>
  <div class="foot"><span class="copy">Copyright © | All Rights Reserved</span><span class="pg"></span><span class="num">10</span><div class="brand"><span class="dot"></span>Veritra</div></div>
</section>

<section class="slide" style="left:410px;top:1189px">
  <div class="photo" style="left:0;top:0;width:386px;height:118px;background:linear-gradient(180deg,#0f2236,#3c5f7c 55%,#9fb7c8)" role="img" aria-label="Photo of rows of metal pipes"></div>
  <div class="card pv" style="left:20px;top:70px;width:107px;height:62px"><h4>Your Text Here</h4><p>Lorem ipsum dolor sit amet, consectetur adipiscing elit, sed do eiusmod tempor incididunt ut labore et dolore magna aliqua.</p></div>
  <div class="card tl" style="left:139px;top:70px;width:107px;height:62px"><h4>Your Text Here</h4><p>Lorem ipsum dolor sit amet, consectetur adipiscing elit, sed do eiusmod tempor incididunt ut labore et dolore magna aliqua.</p></div>
  <div class="card pv" style="left:258px;top:70px;width:107px;height:62px"><h4>Your Text Here</h4><p>Lorem ipsum dolor sit amet, consectetur adipiscing elit, sed do eiusmod tempor incididunt ut labore et dolore magna aliqua.</p></div>
  <div class="abs" style="left:0;top:142px;width:386px;text-align:center;font-family:Poppins,sans-serif;font-size:14px;color:var(--ink)">Company <b style="font-weight:600;color:var(--purple)">Highlights</b></div>
  <p class="abs tiny" style="left:18px;top:166px;width:350px;text-align:center">Lorem ipsum dolor sit amet, consectetur adipiscing elit, sed do eiusmod tempor incididunt ut labore et dolore magna aliqua. Lorem ipsum dolor sit amet, consectetur adipiscing elit, sed do eiusmod tempor incididunt ut labore et dolore magna aliqua. Lorem ipsum dolor sit amet.</p>
  <div class="foot"><span class="copy">Copyright © | All Rights Reserved</span><span class="pg"></span><span class="num">11</span><div class="brand"><span class="dot"></span>Veritra</div></div>
</section>

<section class="slide" style="left:805px;top:1189px">
  <div class="photo" style="left:0;top:0;width:140px;height:217px;background:linear-gradient(160deg,#f1f2f4,#dfe3e8 40%,#2d5d7a 60%,#d8dce2)" role="img" aria-label="Photo of a laptop showing an ocean image"></div>
  <div class="hdr left" style="left:162px;top:38px;width:210px">Add Awesome Title Here<span class="sub">ADD SUBTITLE HERE</span></div>
  <p class="abs tiny" style="left:162px;top:68px;width:205px">Lorem Ipsum is the printing and typesetting industry. Lorem Ipsum has been the industry's standard dummy text ever since the 1500s, when an unknown printer took a galley of type and scrambled it to make a type specimen book.</p>
  <div class="card pv" style="left:112px;top:110px;width:74px;height:80px;text-align:center"><h4 style="margin-top:14px">Project name</h4><p>Lorem ipsum dolor sit amet, nec an dictas equidem appellantur.</p></div>
  <div class="card" style="left:195px;top:110px;width:74px;height:80px;text-align:center;background:#fff;color:var(--text);box-shadow:0 1px 6px rgba(0,0,0,.1)"><h4 style="margin-top:14px;color:var(--ink)">Project name</h4><p>Lorem ipsum dolor sit amet, nec an dictas equidem appellantur.</p></div>
  <div class="card" style="left:278px;top:110px;width:74px;height:80px;text-align:center;background:#fff;color:var(--text);box-shadow:0 1px 6px rgba(0,0,0,.1)"><h4 style="margin-top:14px;color:var(--ink)">Project name</h4><p>Lorem ipsum dolor sit amet, nec an dictas equidem appellantur.</p></div>
  <div class="foot"><span class="pg"></span><span class="num">12</span><div class="brand"><span class="dot"></span>Veritra</div></div>
</section>

<!-- row 5 -->
<section class="slide" style="left:15px;top:1419px">
  <div class="hdr">Add Awesome Title Here<span class="sub">ADD SUBTITLE HERE</span></div>
  <div class="item" style="left:33px;top:64px"><span class="icon-ring"></span><div class="label">Project name</div><p class="tiny">Lorem ipsum dolor sit amet, nec an dictas equidem appellantur, ut has commune accommodare.</p></div>
  <div class="item" style="left:200px;top:64px"><span class="icon-ring"></span><div class="label">Project name</div><p class="tiny">Lorem ipsum dolor sit amet, nec an dictas equidem appellantur, ut has commune accommodare.</p></div>
  <div class="item" style="left:33px;top:105px"><span class="icon-ring"></span><div class="label">Project name</div><p class="tiny">Lorem ipsum dolor sit amet, nec an dictas equidem appellantur, ut has commune accommodare.</p></div>
  <div class="item" style="left:200px;top:105px"><span class="icon-ring"></span><div class="label">Project name</div><p class="tiny">Lorem ipsum dolor sit amet, nec an dictas equidem appellantur, ut has commune accommodare.</p></div>
  <div class="item" style="left:33px;top:146px"><span class="icon-ring"></span><div class="label">Project name</div><p class="tiny">Lorem ipsum dolor sit amet, nec an dictas equidem appellantur, ut has commune accommodare.</p></div>
  <div class="item" style="left:200px;top:146px"><span class="icon-ring"></span><div class="label">Project name</div><p class="tiny">Lorem ipsum dolor sit amet, nec an dictas equidem appellantur, ut has commune accommodare.</p></div>
  <div class="foot"><span class="copy">Copyright © | All Rights Reserved</span><span class="pg"></span><span class="num">13</span><div class="brand"><span class="dot"></span>Veritra</div></div>
</section>

<section class="slide" style="left:410px;top:1419px">
  <div class="photo" style="left:-10px;top:10px;width:160px;height:160px;border-radius:50%;background:radial-gradient(circle at 50% 50%,#3d8fe0,#132b5c 60%,#0b1530);border:4px solid #4d6fc1" role="img" aria-label="Round photo of glowing blue light streaks"></div>
  <div class="hdr left" style="left:168px;top:38px;width:210px">Add Awesome Title Here<span class="sub">ADD SUBTITLE HERE</span></div>
  <p class="abs tiny" style="left:168px;top:68px;width:200px">Sed do eiusmod tempor incididunt ut labore et dolore magna aliqua. Lorem ipsum dolor sit amet, consectetur adipiscing elit, sed do eiusmod tempor incididunt ut labore et dolore magna aliqua. Ut enim ad minim veniam, quis nostrud exercitation ullamco laboris nisi ut aliquip.</p>
  <div class="abs" style="left:168px;top:136px;width:16px;height:16px;border-radius:50%;background:var(--purple)"></div>
  <div class="abs" style="left:188px;top:135px;width:70px"><div class="label">Project name</div><p class="tiny">Lorem ipsum dolor sit amet, nec an dictas equidem.</p></div>
  <div class="abs" style="left:272px;top:136px;width:16px;height:16px;border-radius:50%;background:var(--purple)"></div>
  <div class="abs" style="left:292px;top:135px;width:70px"><div class="label">Project name</div><p class="tiny">Lorem ipsum dolor sit amet, nec an dictas equidem.</p></div>
  <div class="foot"><span class="copy">Copyright © | All Rights Reserved</span><span class="pg"></span><span class="num">14</span><div class="brand"><span class="dot"></span>Veritra</div></div>
</section>

<section class="slide" style="left:805px;top:1419px">
  <div class="hdr">Add Awesome Title Here<span class="sub">ADD SUBTITLE HERE</span></div>
  <svg class="abs" style="left:50px;top:70px" width="105" height="105" viewBox="0 0 105 105">
    <circle cx="52.5" cy="52.5" r="42" fill="none" stroke="#e9eaf3" stroke-width="11"/>
    <circle cx="52.5" cy="52.5" r="42" fill="none" stroke="url(#ring72)" stroke-width="11" stroke-dasharray="190 264" transform="rotate(-90 52.5 52.5)"/>
    <defs><linearGradient id="ring72" x1="0" y1="0" x2="1" y2="1"><stop offset="0" stop-color="#24c1d6"/><stop offset="1" stop-color="#6a56aa"/></linearGradient></defs>
  </svg>
  <div class="abs pct" style="left:50px;top:107px;width:105px;text-align:center;font-size:23px">72%</div>
  <div class="item" style="left:198px;top:80px;width:170px"><span class="icon-ring"></span><p class="tiny">Lorem Ipsum the printing and typesetting industry. Lorem Ipsum has been the industry's standard dummy text ever since the 1500s, when an unknown printer took.</p></div>
  <div class="item" style="left:198px;top:116px;width:170px"><span class="icon-ring"></span><p class="tiny">Lorem Ipsum the printing and typesetting industry. Lorem Ipsum has been the industry's standard dummy text ever since the 1500s, when an unknown printer took.</p></div>
  <div class="item" style="left:198px;top:152px;width:170px"><span class="icon-ring"></span><p class="tiny">Lorem Ipsum the printing and typesetting industry. Lorem Ipsum has been the industry's standard dummy text ever since the 1500s, when an unknown printer took.</p></div>
  <div class="foot"><span class="copy">Copyright © | All Rights Reserved</span><span class="pg"></span><span class="num">15</span><div class="brand"><span class="dot"></span>Veritra</div></div>
</section>

<!-- row 6 -->
<section class="slide" style="left:15px;top:1649px">
  <div class="hdr">Add Awesome Title Here<span class="sub">ADD SUBTITLE HERE</span></div>
  <div class="abs" style="left:22px;top:66px;width:52px;height:52px;border-radius:50%;border:3px dotted #24c1d6"></div>
  <div class="abs pct" style="left:22px;top:82px;width:52px;text-align:center;font-size:14px;color:var(--purple)">45%</div>
  <div class="abs label" style="left:22px;top:130px;color:var(--ink)">Your Text Here</div>
  <p class="abs tiny" style="left:22px;top:140px;width:118px">You can simply impress your audience and add a unique zing and appeal to your presentations. Easy to change colors, photos and text.</p>
  <div class="photo" style="left:140px;top:44px;width:246px;height:150px;background:linear-gradient(180deg,#f4f4f6,#e2e4e8)" role="img" aria-label="Photo of a laptop showing a search page"></div>
  <div class="foot"><span class="copy">Copyright © | All Rights Reserved</span><span class="pg"></span><span class="num">16</span><div class="brand"><span class="dot"></span>Veritra</div></div>
</section>

<section class="slide" style="left:410px;top:1649px">
  <div class="head-band" style="height:98px;background:linear-gradient(180deg,#6b52a8,#5a7cc2 70%,#3aa6d4)"></div>
  <div class="hdr on-grad" style="top:56px">Add Awesome Title Here<span class="sub">ADD SUBTITLE HERE</span></div>
  <div class="abs" style="left:52px;top:90px;width:28px;height:28px;border-radius:50%;background:#6c78c4;border:2px solid #fff"></div>
  <div class="abs" style="left:132px;top:90px;width:28px;height:28px;border-radius:50%;background:#6c78c4;border:2px solid #fff"></div>
  <div class="abs" style="left:212px;top:90px;width:28px;height:28px;border-radius:50%;background:#6c78c4;border:2px solid #fff"></div>
  <div class="abs" style="left:292px;top:90px;width:28px;height:28px;border-radius:50%;background:#6c78c4;border:2px solid #fff"></div>
  <div class="abs" style="left:30px;top:128px;width:72px;text-align:center"><div class="label" style="color:var(--ink)">Lorem ipsum dolor</div><p class="tiny">Lorem ipsum dolor sit amet consectetur adipiscing elit sed do eiusmod tempor incididunt ut labore.</p></div>
  <div class="abs" style="left:110px;top:128px;width:72px;text-align:center"><div class="label" style="color:var(--ink)">Lorem ipsum dolor</div><p class="tiny">Lorem ipsum dolor sit amet consectetur adipiscing elit sed do eiusmod tempor incididunt ut labore.</p></div>
  <div class="abs" style="left:190px;top:128px;width:72px;text-align:center"><div class="label" style="color:var(--ink)">Lorem ipsum dolor</div><p class="tiny">Lorem ipsum dolor sit amet consectetur adipiscing elit sed do eiusmod tempor incididunt ut labore.</p></div>
  <div class="abs" style="left:270px;top:128px;width:72px;text-align:center"><div class="label" style="color:var(--ink)">Lorem ipsum dolor</div><p class="tiny">Lorem ipsum dolor sit amet consectetur adipiscing elit sed do eiusmod tempor incididunt ut labore.</p></div>
  <div class="foot"><span class="copy">Copyright © | All Rights Reserved</span><span class="pg"></span><span class="num">17</span><div class="brand"><span class="dot"></span>Veritra</div></div>
</section>

<section class="slide" style="left:805px;top:1649px">
  <div class="hdr">Add Awesome Title Here<span class="sub">ADD SUBTITLE HERE</span></div>
  <div class="abs" style="left:55px;top:70px;font-size:5.5px;color:var(--text);line-height:22px;text-align:right;width:70px">Header Text Here<br>Header Text Here<br>Header Text Here<br>Header Text Here<br>Header Text Here</div>
  <svg class="abs" style="left:116px;top:77px" width="8" height="100"><g fill="#6a6bb8"><circle cx="4" cy="0" r="2"/><circle cx="4" cy="22" r="2"/><circle cx="4" cy="44" r="2"/><circle cx="4" cy="66" r="2"/><circle cx="4" cy="88" r="2"/></g></svg>
  <svg class="abs" style="left:182px;top:40px" width="150" height="150" viewBox="0 0 150 150">
    <circle cx="75" cy="75" r="73" fill="#22c3d6"/>
    <circle cx="75" cy="88" r="58" fill="#5a63b3"/>
    <circle cx="75" cy="100" r="45" fill="#6a56aa"/>
    <circle cx="75" cy="111" r="33" fill="#5f4a9c"/>
    <circle cx="75" cy="122" r="21" fill="#4f3d8a"/>
  </svg>
  <div class="abs" style="left:182px;top:45px;width:150px;text-align:center;font-size:3.5px;color:#fff;line-height:1">
    <div style="margin-top:13px">26.29 M</div><div style="margin-top:25px">20.29 M</div><div style="margin-top:25px">15.29 M</div><div style="margin-top:22px">8.29 M</div><div style="margin-top:16px">60.29 K</div>
  </div>
  <div class="foot"><span class="copy">Copyright © | All Rights Reserved</span><span class="pg"></span><span class="num">18</span><div class="brand"><span class="dot"></span>Veritra</div></div>
</section>

<!-- row 7 -->
<section class="slide" style="left:15px;top:1879px">
  <svg class="abs" style="left:0;top:0" width="220" height="217" viewBox="0 0 220 217">
    <circle cx="90" cy="80" r="42" fill="none" stroke="#e8e9f1" stroke-width="9"/>
    <circle cx="90" cy="80" r="42" fill="none" stroke="#5a6ab8" stroke-width="9" stroke-dasharray="224 264" transform="rotate(-90 90 80)"/>
    <circle cx="152" cy="127" r="37" fill="none" stroke="#e8e9f1" stroke-width="9"/>
    <circle cx="152" cy="127" r="37" fill="none" stroke="#6a56aa" stroke-width="9" stroke-dasharray="139 232" transform="rotate(-90 152 127)"/>
    <circle cx="88" cy="153" r="26" fill="none" stroke="#e8e9f1" stroke-width="7"/>
    <circle cx="88" cy="153" r="26" fill="none" stroke="#24c1d6" stroke-width="7" stroke-dasharray="57 163" transform="rotate(-90 88 153)"/>
  </svg>
  <div class="abs pct" style="left:70px;top:73px;font-size:13px">85<small style="font-size:8px">%</small></div>
  <div class="abs pct" style="left:137px;top:120px;font-size:13px">60<small style="font-size:8px">%</small></div>
  <div class="abs pct" style="left:77px;top:148px;font-size:9px">35<small style="font-size:6px">%</small></div>
  <div class="abs" style="left:226px;top:46px;font-family:Poppins,sans-serif;font-size:17px;font-weight:300">Chart</div>
  <div class="abs" style="left:226px;top:66px;font-size:6px;color:var(--text)">Lorem ipsum dolor sit amet</div>
  <div class="abs pct" style="left:228px;top:90px;font-size:11px;color:var(--purple)">35 %</div>
  <p class="abs tiny" style="left:228px;top:100px;width:135px;padding-left:24px;margin-top:-10px">Lorem ipsum dolor sit amet, consectetur adipiscing elit, sed do eiusmod tempor incididunt ut labore et dolore magna aliqua.</p>
  <p class="abs tiny" style="left:236px;top:130px;width:125px">▸ Lorem ipsum dolor sit amet, consectetur adipiscing elit. Lorem ipsum dolor sit amet.</p>
  <p class="abs tiny" style="left:236px;top:152px;width:125px">▸ Lorem ipsum dolor sit amet, consectetur adipiscing elit. Lorem ipsum dolor sit amet.</p>
  <div class="foot"><span class="copy">Copyright © | All Rights Reserved</span><span class="pg"></span><span class="num">19</span><div class="brand"><span class="dot"></span>Veritra</div></div>
</section>

<section class="slide" style="left:410px;top:1879px">
  <div class="hdr">Add Awesome Title Here<span class="sub">ADD SUBTITLE HERE</span></div>
  <div class="abs tiny" style="left:24px;top:55px;width:150px;text-align:justify">
    <p style="margin-bottom:4px">Lorem ipsum dolor sit amet, consectetur adipiscing elit, sed do eiusmod tempor incididunt ut labore et dolore magna aliqua. Lorem ipsum dolor sit amet, consectetur adipiscing elit, sed do eiusmod tempor incididunt ut labore et dolore magna aliqua.</p>
    <p>Sed do eiusmod tempor incididunt ut labore et dolore magna aliqua. Lorem ipsum dolor sit amet, consectetur adipiscing elit, sed do eiusmod tempor incididunt ut labore et dolore magna aliqua. Lorem ipsum dolor sit amet, consectetur adipiscing elit, sed do eiusmod tempor incididunt ut labore et dolore magna aliqua. Ut enim ad minim veniam, quis nostrud exercitation ullamco laboris nisi ut aliquip.</p>
  </div>
  <div class="card pv" style="left:194px;top:60px;width:168px;height:50px;text-align:center;display:flex;align-items:center"><p>Lorem Ipsum the printing and typesetting industry. Lorem Ipsum has been the industry's standard dummy text ever since the 1500s, when an unknown printer took</p></div>
  <div class="card tl" style="left:194px;top:124px;width:168px;height:50px;text-align:center;display:flex;align-items:center"><p>Lorem Ipsum the printing and typesetting industry. Lorem Ipsum has been the industry's standard dummy text ever since the 1500s, when an unknown printer took</p></div>
  <div class="foot"><span class="copy">Copyright © | All Rights Reserved</span><span class="pg"></span><span class="num">20</span><div class="brand"><span class="dot"></span>Veritra</div></div>
</section>

<section class="slide" style="left:805px;top:1879px">
  <div class="photo" style="left:0;top:0;width:160px;height:217px;background:linear-gradient(180deg,#1fc0d2,#12a8c4 55%,#1b5c9b)" role="img" aria-label="Photo of a glowing blue robotic hand"></div>
  <div class="card tl" style="left:20px;top:128px;width:70px;height:52px;border-radius:0;text-align:center;background:#22b8cf"><div class="pct" style="color:#fff;font-size:10px">7,500+</div><h4 style="margin:1px 0">Your Stats</h4><p style="font-size:3px">Lorem ipsum dolor sit amet, nec an dictas equidem.</p></div>
  <div class="card pv" style="left:103px;top:128px;width:72px;height:52px;border-radius:0;text-align:center"><div class="pct" style="color:#fff;font-size:10px">6,000+</div><h4 style="margin:1px 0">Your Text</h4><p style="font-size:3px">Lorem ipsum dolor sit amet, nec an dictas equidem.</p></div>
  <div class="hdr left" style="left:196px;top:34px;width:185px">Add Awesome Title Here<span class="sub">ADD SUBTITLE HERE</span></div>
  <p class="abs tiny" style="left:196px;top:62px;width:172px">Lorem ipsum dolor sit amet, consectetur adipiscing elit, sed do eiusmod tempor incididunt ut labore et dolore magna aliqua. Lorem ipsum dolor sit amet, consectetur adipiscing elit.</p>
  <div class="item" style="left:196px;top:120px;width:172px"><span class="icon-ring" style="width:10px;height:10px"></span><p class="tiny" style="margin-left:14px">Lorem ipsum dolor sit amet, consectetur adipiscing elit, sed do eiusmod tempor incididunt ut labore.</p></div>
  <div class="item" style="left:196px;top:146px;width:172px"><span class="icon-ring" style="width:10px;height:10px"></span><p class="tiny" style="margin-left:14px">Lorem ipsum dolor sit amet, consectetur adipiscing elit, sed do eiusmod tempor incididunt ut labore.</p></div>
  <div class="item" style="left:196px;top:172px;width:172px"><span class="icon-ring" style="width:10px;height:10px"></span><p class="tiny" style="margin-left:14px">Lorem ipsum dolor sit amet, consectetur adipiscing elit, sed do eiusmod tempor incididunt ut labore.</p></div>
  <div class="foot"><span class="pg"></span><span class="num">21</span><div class="brand"><span class="dot"></span>Veritra</div></div>
</section>

<!-- row 8 -->
<section class="slide" style="left:15px;top:2109px">
  <div class="hdr left" style="left:30px;top:58px;width:180px">Add Awesome Title Here<span class="sub">ADD SUBTITLE HERE</span></div>
  <p class="abs tiny" style="left:30px;top:86px;width:110px">Lorem ipsum dolor sit amet, consectetur adipiscing elit, sed do eiusmod tempor incididunt ut labore et dolore magna aliqua. Lorem ipsum dolor sit amet, consectetur adipiscing elit, sed do eiusmod tempor incididunt ut labore et dolore magna aliqua.</p>
  <div class="bubble" style="left:275px;top:35px;width:80px;height:80px;background:#24c1d6"><b>800.000 USD</b><span>Lorem ipsum dolor sit amet, consectetur adipiscing elit.</span></div>
  <div class="bubble" style="left:250px;top:97px;width:62px;height:62px;background:#6a56aa"><b>4000 USD</b><span>Lorem ipsum dolor sit amet, consectetur.</span></div>
  <div class="bubble" style="left:218px;top:140px;width:58px;height:58px;background:#6a56aa"><b>3M USD</b><span>Lorem ipsum dolor sit amet.</span></div>
  <p class="abs tiny" style="left:222px;top:20px;width:52px;text-align:center">Lorem ipsum dolor sit amet, consectetur adipiscing elit sed do.</p>
  <p class="abs tiny" style="left:190px;top:82px;width:52px;text-align:center">Lorem ipsum dolor sit amet, consectetur adipiscing elit sed do.</p>
  <p class="abs tiny" style="left:165px;top:128px;width:52px;text-align:center">Lorem ipsum dolor sit amet, consectetur adipiscing elit sed do.</p>
  <div class="foot"><span class="copy">Copyright © | All Rights Reserved</span><span class="pg"></span><span class="num">22</span><div class="brand"><span class="dot"></span>Veritra</div></div>
</section>

<section class="slide" style="left:410px;top:2109px">
  <div class="head-band"></div><div class="tab"></div>
  <div class="hdr on-grad">Add Awesome Title Here<span class="sub">ADD SUBTITLE HERE</span></div>
  <p class="abs tiny" style="left:50px;top:68px;width:286px;text-align:center">Lorem Ipsum the printing and typesetting industry. Lorem Ipsum has been the industry's standard dummy text ever since the 1500s, when an unknown printer took a galley of type and scrambled it to make a type specimen book. It has survived not only five centuries.</p>
  <svg class="abs" style="left:0;top:95px" width="386" height="70" viewBox="0 0 386 70">
    <g fill="none" stroke-width="5">
      <circle cx="108" cy="35" r="27" stroke="#e8e9f1"/><circle cx="108" cy="35" r="27" stroke="#6a56aa" stroke-dasharray="85 170" transform="rotate(-90 108 35)"/>
      <circle cx="189" cy="35" r="27" stroke="#e8e9f1"/><circle cx="189" cy="35" r="27" stroke="#24c1d6" stroke-dasharray="127 170" transform="rotate(-90 189 35)"/>
      <circle cx="270" cy="35" r="27" stroke="#e8e9f1"/><circle cx="270" cy="35" r="27" stroke="#6a56aa" stroke-dasharray="68 170" transform="rotate(-90 270 35)"/>
    </g>
  </svg>
  <div class="abs pct" style="left:81px;top:121px;width:54px;text-align:center;font-size:14px;font-weight:500">50%</div>
  <div class="abs pct" style="left:162px;top:121px;width:54px;text-align:center;font-size:14px;font-weight:500">75%</div>
  <div class="abs pct" style="left:243px;top:121px;width:54px;text-align:center;font-size:14px;font-weight:500">40%</div>
  <p class="abs tiny" style="left:83px;top:168px;width:50px;text-align:center">Lorem ipsum dolor amet consectetur dolor</p>
  <p class="abs tiny" style="left:164px;top:168px;width:50px;text-align:center">Lorem ipsum dolor amet consectetur dolor</p>
  <p class="abs tiny" style="left:245px;top:168px;width:50px;text-align:center">Lorem ipsum dolor amet consectetur dolor</p>
  <div class="foot"><span class="copy">Copyright © | All Rights Reserved</span><span class="pg"></span><span class="num">23</span><div class="brand"><span class="dot"></span>Veritra</div></div>
</section>

<section class="slide" style="left:805px;top:2109px">
  <div class="photo" style="left:0;top:0;width:100px;height:217px;background:repeating-linear-gradient(180deg,#d6d6d8 0 7px,#5b5b60 7px 14px)" role="img" aria-label="Overhead photo of people on a crosswalk"></div>
  <div class="abs" style="left:84px;top:0;width:40px;height:217px;background:rgba(107,92,174,.95)"></div>
  <div class="abs" style="left:84px;top:0;width:40px;height:217px;display:flex;align-items:center;justify-content:center"><div style="transform:rotate(-90deg);white-space:nowrap;font-family:Poppins,sans-serif;font-weight:600;font-size:13px;color:#fff">Table of Content</div></div>
  <div class="abs" style="left:206px;top:36px;font-size:6px;color:var(--text);line-height:21px">
    <div><b style="color:var(--ink)">01</b>&nbsp; Add your content here</div>
    <div><b style="color:var(--ink)">02</b>&nbsp; Add your content here</div>
    <div><b style="color:var(--ink)">03</b>&nbsp; Add your content here</div>
    <div><b style="color:var(--ink)">04</b>&nbsp; Add your content here</div>
    <div><b style="color:var(--ink)">05</b>&nbsp; Add your content here</div>
    <div><b style="color:var(--ink)">06</b>&nbsp; Add your content here</div>
    <div><b style="color:var(--ink)">07</b>&nbsp; Add your content here</div>
  </div>
  <div class="foot"><span class="pg"></span><span class="num">24</span><div class="brand"><span class="dot"></span>Veritra</div></div>
</section>

<!-- row 9 -->
<section class="slide last" style="left:208px">
  <div class="tab"></div>
  <div class="hdr" style="top:12px">Add Awesome Title Here<span class="sub">ADD SUBTITLE HERE</span></div>
  <div class="abs" style="left:48px;top:60px;width:42px;height:42px;border-radius:50%;background:#cfd3dc" role="img" aria-label="Team member portrait"></div>
  <div class="abs" style="left:128px;top:60px;width:42px;height:42px;border-radius:50%;background:#cfd3dc" role="img" aria-label="Team member portrait"></div>
  <div class="abs" style="left:210px;top:60px;width:42px;height:42px;border-radius:50%;background:#cfd3dc" role="img" aria-label="Team member portrait"></div>
  <div class="abs" style="left:290px;top:60px;width:42px;height:42px;border-radius:50%;background:#cfd3dc" role="img" aria-label="Team member portrait"></div>
  <div class="abs" style="left:34px;top:110px;width:70px;text-align:center"><div class="label">YOUR NAME</div><div style="font-size:4.5px;margin-bottom:3px">CEO and Director</div><p class="tiny">Lorem ipsum dolor sit amet, consectetur adipiscing elit. Donec mauris lorem, vestibulum ut dui.</p></div>
  <div class="abs" style="left:114px;top:110px;width:70px;text-align:center"><div class="label">YOUR NAME</div><div style="font-size:4.5px;margin-bottom:3px">CEO and Director</div><p class="tiny">Lorem ipsum dolor sit amet, consectetur adipiscing elit. Donec mauris lorem, vestibulum ut dui.</p></div>
  <div class="abs" style="left:196px;top:110px;width:70px;text-align:center"><div class="label">YOUR NAME</div><div style="font-size:4.5px;margin-bottom:3px">CEO and Director</div><p class="tiny">Lorem ipsum dolor sit amet, consectetur adipiscing elit. Donec mauris lorem, vestibulum ut dui.</p></div>
  <div class="abs" style="left:276px;top:110px;width:70px;text-align:center"><div class="label">YOUR NAME</div><div style="font-size:4.5px;margin-bottom:3px">CEO and Director</div><p class="tiny">Lorem ipsum dolor sit amet, consectetur adipiscing elit. Donec mauris lorem, vestibulum ut dui.</p></div>
  <div class="foot"><span class="copy">Copyright © | All Rights Reserved</span><span class="pg"></span><span class="num">25</span><div class="brand"><span class="dot"></span>Veritra</div></div>
</section>

<section class="slide last" style="left:607px">
  <div class="photo" style="left:0;top:0;width:386px;height:217px;background:linear-gradient(150deg,#e9ebef,#f7f8fa 50%,#dcdfe5)" role="img" aria-label="Pale photo of a glass building ceiling"></div>
  <div class="abs" style="left:52px;top:56px;width:104px;height:22px;background:var(--purple);display:flex;align-items:center;gap:8px;padding-left:10px;font-size:4px;color:#fff">
    <svg width="7" height="7" viewBox="0 0 10 10"><circle cx="5" cy="5" r="4" fill="none" stroke="#fff"/><line x1="1" y1="5" x2="9" y2="5" stroke="#fff"/></svg>www.veritra-health.com</div>
  <div class="abs" style="left:52px;top:80px;width:104px;height:86px;background:#fff;font-size:4px;color:var(--text)">
    <div style="display:flex;align-items:center;gap:8px;padding:7px 10px"><svg width="6" height="8" viewBox="0 0 6 8"><path d="M3 0a3 3 0 0 0-3 3c0 2 3 5 3 5s3-3 3-5a3 3 0 0 0-3-3z" fill="none" stroke="#555" stroke-width=".8"/></svg>Here to write your<br>Company adress</div>
    <div style="display:flex;align-items:center;gap:8px;padding:7px 10px;border-top:1px solid var(--line)"><svg width="7" height="7" viewBox="0 0 10 10"><path d="M2 1l2 2-1 1.5c.8 1.5 2 2.7 3.5 3.5L8 7l2 2-1.5 1C4 10 0 6 0 2.5z" fill="#555"/></svg>(555) 014-2290</div>
    <div style="display:flex;align-items:center;gap:8px;padding:7px 10px;border-top:1px solid var(--line)"><svg width="8" height="6" viewBox="0 0 8 6"><rect x=".4" y=".4" width="7.2" height="5.2" fill="none" stroke="#555" stroke-width=".8"/><path d="M.4.4L4 3.4 7.6.4" fill="none" stroke="#555" stroke-width=".8"/></svg>hello@veritra-health.com</div>
  </div>
  <div class="socials" style="left:-117px;top:170px;color:var(--purple)"><i style="border-radius:2px"></i><i style="border-radius:2px"></i><i style="border-radius:2px"></i><i style="border-radius:2px"></i></div>
  <div class="abs brand" style="left:190px;top:90px;width:190px;font-size:24px"><span class="dot" style="width:24px;height:24px"></span>Veritra</div>
</section>

</body>
</html>
```